CV Template

We need a graphic design to our new CV templates for our consultants. We are a small young Danish upcoming IT-business company making software solutions for our customers etc. You can visit our new website here: dev.sol-brovaerk.com, then you can see our web design, colors etc. I have attached a file for your inspiration :-) In the presentation I would like to have a picture of the employee, some text who descripe the profile/consultant and then I imagine that there is a table where we can write the employee's skills etc.

I would like the design to be "fresh & catchy" :-)

Looking forward to hear from you.

Best regards,
Hanne

```html
<!DOCTYPE html>
<html lang="da">
<head>
<meta charset="utf-8">
<title>CV – Kompetencer</title>
<link href="https://fonts.googleapis.com/css2?family=Carlito:wght@400;700&display=swap" rel="stylesheet">
<style>
:root{
  --page:#eef2f7;
  --panel:#ffffff;
  --ink:#111111;
  --accent:#1ec8f0;
  --brand:#2b6f9a;
  --lvl1:#ffff00;
  --lvl2:#ffe100;
  --lvl3:#ffc000;
  --lvl4:#ff9900;
  --lvl5:#ff0000;
}
*{margin:0;padding:0;box-sizing:border-box}
html,body{width:902px;height:1200px;overflow:hidden}
body{background:var(--page);font-family:"Carlito",Calibri,sans-serif;color:var(--ink);position:relative}
.abs{position:absolute}
.brand{position:absolute;left:666px;top:80px;color:var(--brand)}
.brand-name{font-size:25px;letter-spacing:1px;line-height:1}
.brand-tagline{font-size:8.5px;letter-spacing:.6px;margin-top:3px}
.panel{position:absolute;left:57px;top:165px;width:794px;height:765px;background:var(--panel);border-radius:52px}
.title{left:145px;top:279px;font-size:19px;font-weight:700;color:var(--accent)}
.title-rule{left:145px;top:303px;width:198px;height:1px;background:#cfd8e0}
.level-head{top:302px;font-size:13px;line-height:16px;width:120px;transform-origin:left bottom;transform:rotate(-90deg);white-space:nowrap}
.col-head{font-size:14px}
.group{font-size:14px;font-weight:700;color:var(--accent)}
.label{right:561px;font-size:14px;text-align:right;line-height:18.5px;white-space:nowrap}
.bar{left:350px;display:flex;height:18.5px}
.bar span{width:37px;height:100%}
.bar .l1{background:var(--lvl1)}.bar .l2{background:var(--lvl2)}.bar .l3{background:var(--lvl3)}.bar .l4{background:var(--lvl4)}.bar .l5{background:var(--lvl5)}
.years{left:570px;width:30px;text-align:center;font-size:14px;line-height:18.5px}
.divider{left:635px;width:1px;background:#333}
.legend{left:350px;top:684px;font-size:11px;line-height:14.6px}
.rule{left:133px;top:775px;width:643px;height:1px;background:var(--accent)}
.facts{left:0;top:796px;width:902px;font-size:13.5px;line-height:18.5px}
.fact{display:flex}
.fact dt{width:347px;text-align:right;font-weight:700;color:var(--accent);padding-right:16px}
.fact dd{flex:1}
.env dd{font-size:15px}
.footer{left:92px;top:1090px;font-size:12px;font-weight:700;display:flex}
.footer span{display:inline-block}
</style>
</head>
<body>
<header class="brand">
  <div class="brand-name">Sol Brovaerk</div>
  <div class="brand-tagline">Kvalitet i hver eneste kodelinje</div>
</header>

<main class="panel"></main>

<section class="skills">
  <div class="abs title">Kompetenceområder</div>
  <div class="abs title-rule"></div>

  <div class="abs level-head" style="left:361px">Begynder niveau</div>
  <div class="abs level-head" style="left:397px">Basisniveau</div>
  <div class="abs level-head" style="left:435px">Professionel</div>
  <div class="abs level-head" style="left:471px">Supervisorniveau</div>
  <div class="abs level-head" style="left:509px">Ekspertniveau</div>
  <div class="abs col-head" style="left:542px;top:308px">Års erfaring</div>
  <div class="abs col-head" style="left:644px;top:308px">Sidst anvendt</div>

  <div class="abs group" style="left:145px;top:327px">Database Administration</div>
  <div class="abs label" style="top:344px">KvikDB</div><div class="abs bar" style="top:344px"><span class="l1"></span><span class="l2"></span><span class="l3"></span><span class="l4"></span><span class="l5"></span></div><div class="abs years" style="top:344px">9</div>
  <div class="abs label" style="top:362.5px">LynDB</div><div class="abs bar" style="top:362.5px"><span class="l1"></span><span class="l2"></span><span class="l3"></span><span class="l4"></span><span class="l5"></span></div><div class="abs years" style="top:362.5px">9</div>
  <div class="abs label" style="top:381px">TarnDB</div><div class="abs bar" style="top:381px"><span class="l1"></span><span class="l2"></span><span class="l3"></span></div><div class="abs years" style="top:381px">9</div>
  <div class="abs label" style="top:399.5px">Arkiv DB</div><div class="abs bar" style="top:399.5px"><span class="l1"></span><span class="l2"></span></div><div class="abs years" style="top:399.5px">3</div>
  <div class="abs label" style="top:418px">Paralex</div><div class="abs bar" style="top:418px"><span class="l1"></span><span class="l2"></span><span class="l3"></span><span class="l4"></span><span class="l5"></span></div><div class="abs years" style="top:418px">8</div>
  <div class="abs label" style="top:436.5px">Implementering</div><div class="abs bar" style="top:436.5px"><span class="l1"></span><span class="l2"></span><span class="l3"></span><span class="l4"></span></div>
  <div class="abs divider" style="top:344px;height:111px"></div>

  <div class="abs group" style="left:172px;top:456px">Programmeringssprog</div>
  <div class="abs label" style="top:473px">K#</div><div class="abs bar" style="top:473px"><span class="l1"></span><span class="l2"></span><span class="l3"></span><span class="l4"></span><span class="l5"></span></div><div class="abs years" style="top:473px">7</div>
  <div class="abs label" style="top:491.5px">Visuel Kode</div><div class="abs bar" style="top:491.5px"><span class="l1"></span><span class="l2"></span></div><div class="abs years" style="top:491.5px">3</div>
  <div class="abs label" style="top:510px">Kava</div><div class="abs bar" style="top:510px"><span class="l1"></span><span class="l2"></span></div><div class="abs years" style="top:510px">4</div>
  <div class="abs label" style="top:528.5px">VKScript</div><div class="abs bar" style="top:528.5px"><span class="l1"></span><span class="l2"></span><span class="l3"></span><span class="l4"></span></div><div class="abs years" style="top:528.5px">5</div>
  <div class="abs label" style="top:547px">Hypra</div><div class="abs bar" style="top:547px"><span class="l1"></span><span class="l2"></span><span class="l3"></span><span class="l4"></span><span class="l5"></span></div><div class="abs years" style="top:547px">7</div>
  <div class="abs divider" style="top:473px;height:93px"></div>

  <div class="abs group" style="left:270px;top:567px">Andre</div>
  <div class="abs label" style="top:584px">Projektledelse</div><div class="abs bar" style="top:584px"><span class="l1"></span><span class="l2"></span><span class="l3"></span><span class="l4"></span><span class="l5"></span></div><div class="abs years" style="top:584px">7</div>
  <div class="abs label" style="top:603px">System drift/<br>Administration</div><div class="abs bar" style="top:602.5px;height:37px"><span class="l1"></span></div><div class="abs years" style="top:603px">4</div>
  <div class="abs label" style="top:640px">Webservice</div><div class="abs bar" style="top:639.5px"><span class="l1"></span><span class="l2"></span><span class="l3"></span><span class="l4"></span><span class="l5"></span></div><div class="abs years" style="top:640px">5</div>
  <div class="abs divider" style="top:584px;height:74px"></div>

  <div class="abs legend">
    <div>Begynder niveau: Begrænset kendskab</div>
    <div>Basisniveau: Erfaring på bruger eller uddannelsesniveau</div>
    <div>Professionel: Arbejder selvstændigt</div>
    <div>Supervisorniveau: Kan hjælpe og træne andre</div>
    <div>Ekspertniveau: Indgående kendskab</div>
  </div>

  <div class="abs rule"></div>

  <dl class="abs facts">
    <div class="fact"><dt>Primære udviklingssprog:</dt><dd>K#, Visuel Kode, Kava, VKScript, Hypra</dd></div>
    <div class="fact"><dt>Primære udviklingsværktøjer:</dt><dd>K#, Hypra, KavaScript, ASX, VK, KvikDB, LynDB, Arkiv DB.<br>Derudover kendskab til: K++, Pasko.</dd></div>
    <div class="fact"><dt>Databaseerfaring:</dt><dd>KvikDB, LynDB, TarnDB, Arkiv DB, Paralex.</dd></div>
    <div class="fact env"><dt>Miljøer:</dt><dd>Skyline OS, WEB, Lynx Server/Hypra, Ixa/ASX.</dd></div>
  </dl>
</section>

<footer class="abs footer">
  <span style="width:112px">Sol-Brovaerk ApS</span>
  <span style="width:108px">Solsikkevej 12</span>
  <span style="width:141px">2300 København S.</span>
  <span style="width:146px">Tel: +45 20 40 60 80</span>
  <span>www.sol-brovaerk.dk</span>
</footer>
</body>
</html>
```